Product labels for new supplements business targeting high performing creative people

I need a label design for different supplements like Whey, BCAA, Melatonin etc. that I could customize for each use case separately.

The brand is called moonquell.life, and it would be the first design of the labels. We haven't sold any products yet, but the target audience is people with growth mindset, people who want to be as efficient as possible and are constantly looking to improve their lifestyle. As part of that, they are also working out, but don't know much about supplements yet. Mostly people between 20-34.

I don't have a too specific idea of the expected design, though it should be light, warm, smart and minimalist, maybe have some patterns. It should looks smart and clean (and expensive). Orange and golden might be the additional colors for white. I have attached the templates of some products that I plan to sell and also the logo of the brand.

Here's what I have used for inspiration:
Brands that I like and are somewhat similar in concept: https://www.vantrel.com/ (!!specially the way they
bring "how the product helps them" in focus, not "what the product is" & https://www.plomi.care/ &
https://www.delvora.com/sport/ & https://en.kalobrine.fr/ &
https://48sketchworks.com/profiles/marenhollowaydesign/designs/617482

Here's how different products look like: https://grenvolt.com/catalog

Target Market(s)

target audience is people with growth mindset, people who want to be as efficient as possible and are constantly looking to improve their lifestyle. As part of that, they are also working out, but don't know much about supplements yet. Mostly people between 20-34.

Industry/Entity Type

Supplements

Font styles to use
Sans Serif

Colors
FFC000
F8CF3A
FAE287
FDF2CF
FEFAEE
F0912C
F2A743
F7CA91
FBE8D2
FDF5EE
EE7325
F08F49
F5BC92
FAE3D3
FDF4ED

Requirements
Must have
• Clean, smart and minimalist design that can be applied for different products in different sizes, like Whey protein, BCAA, vitamins etc. available here: https://grenvolt.com/catalog
Nice to have
• Patterns, expensive look
Should not have
• Doodles, too many colors

```html
<!DOCTYPE html>
<html lang="en">
<head>
<meta charset="utf-8">
<title>moonquell.life — supplement labels</title>
<link rel="stylesheet" href="https://fonts.googleapis.com/css2?family=Montserrat:ital,wght@0,400;0,500;0,600;1,400&family=Quicksand:wght@400;500;700&display=swap">
<style>
  :root {
    --white: #ffffff;
    --label: #fbfbfb;
    --ink: #2b2b2b;
    --orange: #ee7325;
    --orange-deep: #f0391a;
    --orange-light: #f08f49;
    --amber: #f0912c;
    --band: #ff7a1a;
    --faint: #ececec;
  }
  * { box-sizing: border-box; margin: 0; padding: 0; }
  html, body { width: 800px; height: 1200px; overflow: hidden; background: var(--white); }
  .sheet { position: relative; width: 800px; height: 1200px; }

  .halo {
    position: absolute; border-radius: 50%;
    background: linear-gradient(180deg, var(--orange-deep) 0%, var(--orange) 55%, var(--amber) 100%);
    opacity: .9;
  }

  .label {
    position: absolute; background: var(--label);
    border-radius: 4px;
    box-shadow: 0 6px 18px rgba(0,0,0,.08);
    display: flex; flex-direction: column; align-items: center;
    font-family: "Montserrat", sans-serif; color: var(--ink);
  }
  .brand {
    font-family: "Quicksand", sans-serif; font-weight: 700; color: var(--ink);
    display: flex; align-items: center; gap: .35em;
  }
  .brand-dot { width: .7em; height: .7em; border-radius: 50%; background: var(--orange); }
  .product {
    font-family: "Quicksand", sans-serif; font-weight: 500; color: var(--orange-deep);
    line-height: 1; white-space: nowrap;
  }
  .variant { font-weight: 600; letter-spacing: .3em; color: var(--ink); }
  .benefit { display: flex; align-items: center; gap: 4px; margin-top: auto; }
  .benefit-icon { flex: none; border: 1px solid var(--ink); border-radius: 50%; }
  .benefit-text { font-style: italic; color: var(--orange); line-height: 1.25; }
  .net { color: var(--orange-deep); }
  .band {
    background: var(--band); color: var(--white);
    letter-spacing: .35em; text-align: center; white-space: nowrap;
  }

  /* Melatonin */
  .halo--melatonin { left: 118px; top: 118px; width: 220px; height: 220px; }
  .label--melatonin { left: 185px; top: 168px; width: 136px; height: 194px; padding: 36px 8px 8px; }
  .label--melatonin .brand { font-size: 11px; }
  .label--melatonin .product { font-size: 19px; margin-top: 40px; }
  .label--melatonin .dose { font-size: 7px; font-weight: 500; margin-top: 2px; }
  .label--melatonin .benefit-icon { width: 9px; height: 9px; }
  .label--melatonin .benefit-text { font-size: 5px; }
  .label--melatonin .band { font-size: 4px; padding: 2px 5px; margin-top: 24px; }
  .count {
    position: absolute; right: 6px; bottom: 40px; font-size: 3.5px; color: var(--orange);
    writing-mode: vertical-rl; transform: rotate(180deg); letter-spacing: .1em;
  }

  /* Beef protein */
  .halo--beef { left: 405px; top: 400px; width: 330px; height: 330px; }
  .label--beef { left: 464px; top: 469px; width: 207px; height: 194px; padding: 32px 10px 10px; }
  .label--beef .brand { font-size: 13px; }
  .label--beef .product { font-size: 21px; margin-top: 26px; }
  .label--beef .variant { font-size: 8px; margin-top: 2px; }
  .label--beef .benefit-icon { width: 16px; height: 16px; }
  .label--beef .benefit-text { font-size: 5px; }
  .label--beef .net { font-size: 6px; margin-top: 18px; }
  .label--beef .band { font-size: 4px; padding: 2px 8px; margin-top: 4px; }

  /* BCAA */
  .halo--bcaa { left: 75px; top: 740px; width: 390px; height: 390px; }
  .label--bcaa { left: 142px; top: 811px; width: 255px; height: 291px; padding: 56px 14px 14px; }
  .label--bcaa .brand { font-size: 17px; }
  .label--bcaa .product { font-size: 29px; letter-spacing: .22em; margin-top: 40px; font-weight: 400; }
  .label--bcaa .variant { font-size: 12px; margin-top: 4px; }
  .label--bcaa .benefit-icon { width: 14px; height: 14px; }
  .label--bcaa .benefit-text { font-size: 7.5px; }
  .label--bcaa .net { font-size: 8px; margin-top: 30px; }
  .label--bcaa .band { font-size: 6px; padding: 3px 10px; margin-top: 4px; }
</style>
</head>
<body>
<main class="sheet">

  <div class="halo halo--melatonin" aria-hidden="true"></div>
  <section class="label label--melatonin">
    <div class="brand"><span class="brand-dot"></span>moonquell.life</div>
    <h2 class="product">MELATONIN</h2>
    <p class="dose">1 mg</p>
    <div class="benefit">
      <span class="benefit-icon" role="img" aria-label="moon icon"></span>
      <p class="benefit-text">Fall asleep faster<br>Stay asleep longer</p>
    </div>
    <p class="band">DIETARY SUPPLEMENT</p>
    <p class="count">60 TABLETS</p>
  </section>

  <div class="halo halo--beef" aria-hidden="true"></div>
  <section class="label label--beef">
    <div class="brand"><span class="brand-dot"></span>moonquell.life</div>
    <h2 class="product">BEEF PROTEIN</h2>
    <p class="variant">CHOCOLATE</p>
    <div class="benefit">
      <span class="benefit-icon" role="img" aria-label="flexed arm icon"></span>
      <p class="benefit-text">Hydrolyzed beef protein with minimum fat content<br>Promotes muscle gain and helps maintain muscle mass</p>
    </div>
    <p class="net">NET Wt. 900g</p>
    <p class="band">DIETARY SUPPLEMENT</p>
  </section>

  <div class="halo halo--bcaa" aria-hidden="true"></div>
  <section class="label label--bcaa">
    <div class="brand"><span class="brand-dot"></span>moonquell.life</div>
    <h2 class="product">BCAA 2:1:1</h2>
    <p class="variant">WILD BERRY</p>
    <div class="benefit">
      <span class="benefit-icon" role="img" aria-label="molecule icon"></span>
      <p class="benefit-text">Essential branched chain amino acids BCAA<br>Increasses muscle growth, reduces fatigue</p>
    </div>
    <p class="net">NET Wt. 300g</p>
    <p class="band">DIETARY SUPPLEMENT</p>
  </section>

</main>
</body>
</html>
```